PSD Only - Wordpress Magazine Theme Design

We need a design for our new Premuim wordpress Magazine theme design based on our basic wire-frame. The theme will be used by people who run online magazine, news website or just blog in general.

The layout of homepage is showing recent posts in many way which is easy to user to customize the section of their homepage to show their post based on various categories.

2 Page design need (Homepage and Single Post)
Updates

Reason: want to get more designer and I am off for holiday a few days too. Better extend the time for designers as well as me also.

Target Market(s)

General Blogger who want a nice premium theme as well as other content based wesite.

Industry/Entity Type

Online

Font styles to use
Sans Serif

Requirements
Must have
• + Must have 2 page design based on Wireframing. Homepage (home.png) annd Single Post (Single.png)
• + Layout must be based on wireframe.
• + Width 1025px
• + 2 Navigation Menu in Header Must be in different style. When theme goes public, user can choose to have both or only 1 navigation or completely hide both of them.
• + 2 Featured Content Slider as you see in wire-frame. They must be in different style from each other.
• + Those recent news section is only about arrange post in defferent ways which only include post feature image, post title as well as post meta info.
• + Sidebar Widget Must be 300px (not include margin or padding) in order to be able for user to place ads with (300px of width) in sidebar widget)
• + Footer Widget Section should have a bit different colour in order to look different for main layout.
Nice to have
• + Drop down Menu
• + (Optional) Some custom Widget (Based on your imagination and creativity)

```html
<!DOCTYPE html>
<html lang="en">
<head>
<meta charset="utf-8">
<title>Ledger Magazine — Home</title>
<link rel="stylesheet" href="https://fonts.googleapis.com/css2?family=Open+Sans:wght@400;600;700;800&display=swap">
<style>
:root{
  --blue:#2c6be0;
  --blue-dark:#1f55b8;
  --ink:#222;
  --text:#555;
  --muted:#9a9a9a;
  --line:#e3e3e3;
  --panel:#efefef;
  --topbar:#e9e9e9;
  --accent:#f0a81a;
  --footer:#1e1e1e;
  --footer-base:#141414;
  --white:#fff;
}
*{box-sizing:border-box;margin:0;padding:0}
html,body{width:1200px;height:4864px;overflow:hidden}
body{font-family:"Open Sans",Arial,sans-serif;color:var(--text);background:var(--white);position:relative;font-size:11px;line-height:1.5}
a{color:inherit;text-decoration:none}
.abs{position:absolute}
.ph{background:linear-gradient(135deg,#c9b9a6,#8d9aa8 55%,#5f6f80)}
.ph.warm{background:linear-gradient(135deg,#e5cfb6,#b99a80 50%,#7b6a62)}
.ph.cool{background:linear-gradient(135deg,#dfe6ec,#a9b8c6 50%,#6b7d8f)}
.ph.bright{background:linear-gradient(135deg,#f3efe6,#d8c7a2 45%,#9fb3c2)}

/* top bar */
.topbar{left:0;top:0;width:1200px;height:32px;background:var(--topbar);border-bottom:1px solid #ddd}
.topbar .links{position:absolute;left:120px;top:0;display:flex;gap:22px;line-height:32px;font-size:10px;color:#666}
.topbar .social{position:absolute;right:120px;top:9px;display:flex;gap:4px}
.topbar .social span{width:14px;height:14px;background:#8a8a8a;display:block}

/* header */
.brand{left:120px;top:96px;width:260px}
.brand .name{font-size:24px;font-weight:800;color:var(--blue-dark);line-height:1;white-space:nowrap}
.brand .tag{font-size:9px;color:var(--muted);letter-spacing:1px;margin-top:8px}
.banner{left:400px;top:86px;width:672px;height:80px;background:linear-gradient(90deg,#0d3a78,#1f5fb0 60%,#3d82d0)}

/* nav */
.nav{left:120px;top:208px;width:960px;height:40px;background:var(--blue)}
.nav ul{list-style:none;display:flex;height:40px}
.nav li{padding:0 16px;line-height:40px;color:var(--white);font-size:10px;font-weight:600}
.nav li.active{background:#1b1b1b}
.nav .search{position:absolute;right:40px;top:9px;width:150px;height:22px;background:var(--white);font-size:9px;color:#999;padding:4px 8px}
.nav .go{position:absolute;right:8px;top:9px;width:30px;height:22px;background:#1b1b1b;color:#fff;font-size:9px;text-align:center;line-height:22px;font-weight:700}

/* main slider */
.slider-main{left:120px;top:300px;width:960px;height:448px}
.slider-main .caption{position:absolute;right:0;top:190px;width:310px;padding:16px 20px;background:rgba(20,20,20,.82);color:#fff}
.slider-main .caption h2{font-size:20px;font-weight:700;letter-spacing:.5px;margin-bottom:8px}
.slider-main .caption p{font-size:10px;color:#ddd}
.slider-main .arrows{position:absolute;right:14px;bottom:14px;display:flex;gap:4px}
.arrows span{width:24px;height:24px;background:#1b1b1b;display:flex;align-items:center;justify-content:center}

/* content column */
.main{left:120px;top:780px;width:628px;height:3580px;display:flex;flex-direction:column;justify-content:space-between}
.slider-sub{position:relative;height:340px}
.slider-sub .caption{position:absolute;left:30px;top:100px;width:320px;padding:12px 16px;background:rgba(20,20,20,.8);color:#fff}
.slider-sub .caption h2{font-size:19px;font-weight:700;white-space:nowrap}
.slider-sub .dots{display:flex;gap:5px;margin-top:8px}
.slider-sub .dots span{width:7px;height:7px;background:#888;border-radius:50%}
.slider-sub .dots span.on{background:#fff}

.section-bar{height:32px;background:var(--blue);color:#fff;font-size:13px;font-weight:700;line-height:32px;padding-left:12px;margin-bottom:20px}

.post-title{font-size:14px;font-weight:600;color:var(--ink);line-height:1.3}
.meta{font-size:9px;color:var(--muted);margin:4px 0}
.excerpt{font-size:10px;color:var(--text);line-height:1.6}

.grid3{display:grid;grid-template-columns:repeat(3,1fr);gap:20px}
.grid3 .img{height:140px;margin-bottom:12px}
.grid2{display:grid;grid-template-columns:1fr 1fr;gap:20px}
.grid2 .img{height:168px;margin-bottom:12px}

.world{display:flex;gap:20px}
.world-lead{width:380px;flex:none}
.world-lead .img{height:168px;margin-bottom:12px}
.side-list{width:228px}
.mini{display:flex;gap:10px;margin-bottom:18px}
.mini:last-child{margin-bottom:0}
.mini .thumb{width:62px;height:62px;flex:none}
.mini .t{font-size:11px;font-weight:600;color:var(--ink);line-height:1.35}

.recent-grid{display:grid;grid-template-columns:1fr 1fr;column-gap:40px;row-gap:14px}
.recent-grid .mini{margin:0}
.recent-grid .thumb{width:54px;height:54px}

.row-post{display:flex;gap:20px}
.row-post .img{width:240px;height:190px;flex:none}
.btn{display:inline-block;background:var(--blue);color:#fff;font-size:9px;font-weight:700;padding:6px 12px;margin-top:12px}
.meta-row{height:36px;margin:20px 0 24px;border-top:1px solid var(--line);border-bottom:1px solid var(--line);display:flex;gap:26px;align-items:center;font-size:9px;color:var(--muted);padding-left:4px}
.meta-row:last-child{margin-bottom:0}
.meta-row span{display:flex;align-items:center;gap:6px}

.feature .img{height:200px;margin-bottom:16px}
.feature .post-title{font-size:15px}
.pager{font-size:10px;color:var(--blue)}

/* sidebar */
.sidebar{left:780px;top:780px;width:300px;display:flex;flex-direction:column;gap:28px}
.widget{background:var(--panel);padding:18px 20px 22px}
.widget h3{font-size:15px;font-weight:700;color:var(--blue);margin-bottom:14px}
.widget ul{list-style:none}
.widget li{font-size:10px;color:#555;padding:6px 0 6px 14px;position:relative}
.widget li::before{content:"";position:absolute;left:0;top:12px;width:5px;height:5px;border-radius:50%;background:var(--accent)}
.widget li.sub{padding-left:28px}
.widget li.sub::before{left:16px;background:#bbb}
.pop{display:flex;gap:12px;margin-bottom:16px}
.pop:last-child{margin-bottom:0}
.pop .thumb{width:54px;height:54px;flex:none}
.pop .t{font-size:10px;color:#333;line-height:1.4}

/* footer */
.footer{left:0;top:4400px;width:1200px;height:420px;background:var(--footer)}
.fcol{position:absolute;top:36px;width:280px}
.fcol h4{color:#fff;font-size:14px;font-weight:700;margin-bottom:16px}
.fcol ul{list-style:none}
.fcol li{font-size:10px;color:#aaa;padding:4px 0 4px 14px;position:relative}
.fcol li::before{content:"";position:absolute;left:0;top:10px;width:5px;height:5px;border-radius:50%;background:var(--accent)}
.base{left:0;top:4820px;width:1200px;height:44px;background:var(--footer-base);color:#888;font-size:9px}
.base .copy{position:absolute;left:120px;top:15px}
.base .flinks{position:absolute;right:120px;top:15px;display:flex;gap:14px}
</style>
</head>
<body>

<div class="abs topbar">
  <div class="links"><a>About</a><a>Privacy</a><a>Contact</a><a>Login</a><a>Register</a></div>
  <div class="social"><span></span><span></span><span></span><span></span></div>
</div>

<div class="abs brand">
  <div class="name">LEDGER MAGAZINE</div>
  <div class="tag">NEWS · STORIES · IDEAS</div>
</div>
<div class="abs banner" role="img" aria-label="Advertising banner"></div>

<nav class="abs nav">
  <ul>
    <li class="active">HOME</li><li>TRENDINGS</li><li>ABOUT</li><li>PEOPLE</li><li>NEWS</li><li>OUR CATEGORIES</li><li>FORUM</li>
  </ul>
  <div class="search">Search</div>
  <div class="go">GO</div>
</nav>

<section class="abs slider-main ph cool" role="img" aria-label="Featured photo: woman reading at a desk with a coffee cup">
  <div class="caption">
    <h2>IPSUM DOLOR SIT AMET</h2>
    <p>At vero eos et accusamus et iusto odio dignissimos ducimus qui blanditiis praesentium voluptatum deleniti atque corrupti.</p>
  </div>
  <div class="arrows">
    <span><svg width="8" height="10"><path d="M6 1 2 5l4 4" stroke="#fff" stroke-width="2" fill="none"/></svg></span>
    <span><svg width="8" height="10"><path d="M2 1l4 4-4 4" stroke="#fff" stroke-width="2" fill="none"/></svg></span>
  </div>
</section>

<main class="abs main">

  <section class="slider-sub ph warm" role="img" aria-label="Featured photo: two women reading a magazine together">
    <div class="caption">
      <h2>At vereos et accusamus</h2>
      <div class="dots"><span class="on"></span><span></span><span></span></div>
    </div>
  </section>

  <section class="latest">
    <div class="section-bar">Latest News</div>
    <div class="grid3">
      <article><div class="img ph warm" role="img" aria-label="Photo: person reading"></div><div class="post-title">At vero eos et accusa</div><div class="meta">Posted by jon · 2 Comments · 9 hours ago</div><p class="excerpt">On the other hand we denounce with righteous indignation and dislike the printing...</p></article>
      <article><div class="img ph" role="img" aria-label="Photo: woman with glasses reading"></div><div class="post-title">At vero eos et accusa</div><div class="meta">Posted by jon · 2 Comments · 9 hours ago</div><p class="excerpt">On the other hand we denounce with righteous indignation and dislike the printing...</p></article>
      <article><div class="img ph cool" role="img" aria-label="Photo: reader with a newspaper"></div><div class="post-title">At vero eos et accusa</div><div class="meta">Posted by jon · 2 Comments · 9 hours ago</div><p class="excerpt">On the other hand we denounce with righteous indignation and dislike the printing...</p></article>
    </div>
  </section>

  <section class="magazine">
    <div class="section-bar">Our Magazine News</div>
    <div class="grid2">
      <article><div class="img ph bright" role="img" aria-label="Photo: woman reading on a sofa"></div><div class="post-title">On the other hand we denoun</div><div class="meta">Posted by jon · 2 Comments · 9 hours ago</div><p class="excerpt">At vero eos et accusamus et iusto odio dignissimos ducimus qui blanditiis praesentium voluptatum deleniti atque corrupti quos dolores.</p></article>
      <article><div class="img ph warm" role="img" aria-label="Photo: stacked magazines"></div><div class="post-title">On the other hand we denoun</div><div class="meta">Posted by jon · 2 Comments · 9 hours ago</div><p class="excerpt">At vero eos et accusamus et iusto odio dignissimos ducimus qui blanditiis praesentium voluptatum deleniti atque corrupti quos dolores.</p></article>
    </div>
  </section>

  <section class="world-news">
    <div class="section-bar">World News</div>
    <div class="world">
      <article class="world-lead">
        <div class="img ph warm" role="img" aria-label="Photo: couple reading together"></div>
        <div class="post-title">On the other hand we denounce</div>
        <div class="meta">Posted by jon · 2 Comments · 9 hours ago</div>
        <p class="excerpt">At vero eos et accusamus et iusto odio dignissimos ducimus qui blanditiis praesentium voluptatum deleniti atque corrupti quos dolores et quas molestias excepturi sint occaecati cupiditate non provident, similique sunt in culpa qui officia.</p>
      </article>
      <div class="side-list">
        <div class="mini"><div class="thumb ph" role="img" aria-label="Thumbnail photo"></div><div><div class="t">At vero eos et accusamus iusto odio dignissimos...</div><div class="meta">9 hours ago · 2 Comments</div></div></div>
        <div class="mini"><div class="thumb ph cool" role="img" aria-label="Thumbnail photo"></div><div><div class="t">At vero eos et accusamus iusto odio dignissimos...</div><div class="meta">9 hours ago · 2 Comments</div></div></div>
        <div class="mini"><div class="thumb ph warm" role="img" aria-label="Thumbnail photo"></div><div><div class="t">At vero eos et accusamus iusto odio dignissimos...</div><div class="meta">9 hours ago · 2 Comments</div></div></div>
        <div class="mini"><div class="thumb ph bright" role="img" aria-label="Thumbnail photo"></div><div><div class="t">At vero eos et accusamus iusto odio dignissimos...</div><div class="meta">9 hours ago · 2 Comments</div></div></div>
      </div>
    </div>
  </section>

  <section class="recent">
    <div class="section-bar">Recent News</div>
    <div class="recent-grid">
      <div class="mini"><div class="thumb ph warm" role="img" aria-label="Thumbnail photo"></div><div><div class="t">At vero eos et accusamus iusto odio dignissimos...</div><div class="meta">9 hours ago · 2 Comments</div></div></div>
      <div class="mini"><div class="thumb ph" role="img" aria-label="Thumbnail photo"></div><div><div class="t">At vero eos et accusamus iusto odio dignissimos...</div><div class="meta">9 hours ago · 2 Comments</div></div></div>
      <div class="mini"><div class="thumb ph cool" role="img" aria-label="Thumbnail photo"></div><div><div class="t">At vero eos et accusamus iusto odio dignissimos...</div><div class="meta">9 hours ago · 2 Comments</div></div></div>
      <div class="mini"><div class="thumb ph bright" role="img" aria-label="Thumbnail photo"></div><div><div class="t">At vero eos et accusamus iusto odio dignissimos...</div><div class="meta">9 hours ago · 2 Comments</div></div></div>
      <div class="mini"><div class="thumb ph" role="img" aria-label="Thumbnail photo"></div><div><div class="t">At vero eos et accusamus iusto odio dignissimos...</div><div class="meta">9 hours ago · 2 Comments</div></div></div>
      <div class="mini"><div class="thumb ph warm" role="img" aria-label="Thumbnail photo"></div><div><div class="t">At vero eos et accusamus iusto odio dignissimos...</div><div class="meta">9 hours ago · 2 Comments</div></div></div>
      <div class="mini"><div class="thumb ph bright" role="img" aria-label="Thumbnail photo"></div><div><div class="t">At vero eos et accusamus iusto odio dignissimos...</div><div class="meta">9 hours ago · 2 Comments</div></div></div>
      <div class="mini"><div class="thumb ph cool" role="img" aria-label="Thumbnail photo"></div><div><div class="t">At vero eos et accusamus iusto odio dignissimos...</div><div class="meta">9 hours ago · 2 Comments</div></div></div>
    </div>
  </section>

  <section class="recent-magazine">
    <div class="section-bar">Recent Magazine News</div>
    <article class="row-post">
      <div class="img ph bright" role="img" aria-label="Photo: woman reading a book"></div>
      <div><div class="post-title">On the other hand we lorem ipbsu</div><div class="meta">Posted by jon · 2 Comments · 9 hours ago</div><p class="excerpt">At vero eos et accusamus et iusto odio dignissimos ducimus qui blanditiis praesentium voluptatum deleniti atque corrupti quos dolores et quas molestias excepturi sint occaecati.</p><a class="btn">READ MORE</a></div>
    </article>
    <div class="meta-row">
      <span><svg width="10" height="10"><rect x="1" y="2" width="8" height="7" fill="none" stroke="#f0a81a" stroke-width="1.4"/></svg>June 5, 2015</span>
      <span><svg width="10" height="10"><path d="M1 1h8v6H4L2 9V7H1z" fill="#f0a81a"/></svg>24 Comments</span>
      <span><svg width="10" height="10"><path d="M1 2h3l1 1h4v6H1z" fill="#f0a81a"/></svg>Public news</span>
      <span><svg width="12" height="10"><ellipse cx="6" cy="5" rx="5" ry="3.5" fill="none" stroke="#f0a81a" stroke-width="1.4"/><circle cx="6" cy="5" r="1.5" fill="#f0a81a"/></svg>24 Views</span>
      <span><svg width="10" height="10"><path d="M5 9 1 5a2 2 0 0 1 4-3 2 2 0 0 1 4 3z" fill="#f0a81a"/></svg>10</span>
    </div>
    <article class="row-post">
      <div class="img ph" role="img" aria-label="Photo: person reading a tablet"></div>
      <div><div class="post-title">On the other hand we lorem ipbsu</div><div class="meta">Posted by jon · 2 Comments · 9 hours ago</div><p class="excerpt">At vero eos et accusamus et iusto odio dignissimos ducimus qui blanditiis praesentium voluptatum deleniti atque corrupti quos dolores et quas molestias excepturi sint occaecati.</p><a class="btn">READ MORE</a></div>
    </article>
    <div class="meta-row">
      <span><svg width="10" height="10"><rect x="1" y="2" width="8" height="7" fill="none" stroke="#f0a81a" stroke-width="1.4"/></svg>June 5, 2015</span>
      <span><svg width="10" height="10"><path d="M1 1h8v6H4L2 9V7H1z" fill="#f0a81a"/></svg>24 Comments</span>
      <span><svg width="10" height="10"><path d="M1 2h3l1 1h4v6H1z" fill="#f0a81a"/></svg>Public news</span>
      <span><svg width="12" height="10"><ellipse cx="6" cy="5" rx="5" ry="3.5" fill="none" stroke="#f0a81a" stroke-width="1.4"/><circle cx="6" cy="5" r="1.5" fill="#f0a81a"/></svg>24 Views</span>
      <span><svg width="10" height="10"><path d="M5 9 1 5a2 2 0 0 1 4-3 2 2 0 0 1 4 3z" fill="#f0a81a"/></svg>10</span>
    </div>
  </section>

  <section class="featured">
    <div class="section-bar">Featured Blog News</div>
    <article class="feature">
      <div class="img ph warm" role="img" aria-label="Photo: people reading in a bookshop"></div>
      <div class="post-title">At vero eos et accusamus et iusto odio dignissimos ducimus quis the lorem</div>
      <div class="meta">Posted by jon · 2 Comments · 9 hours ago</div>
      <p class="excerpt">At vero eos et accusamus et iusto odio dignissimos ducimus qui blanditiis praesentium voluptatum deleniti atque corrupti quos dolores et quas molestias excepturi sint occaecati cupiditate non provident, similique sunt in culpa qui officia deserunt mollitia animi.</p>
      <a class="btn">READ MORE</a>
    </article>
    <div class="meta-row">
      <span><svg width="10" height="10"><rect x="1" y="2" width="8" height="7" fill="none" stroke="#f0a81a" stroke-width="1.4"/></svg>June 5, 2015</span>
      <span><svg width="10" height="10"><path d="M1 1h8v6H4L2 9V7H1z" fill="#f0a81a"/></svg>24 Comments</span>
      <span><svg width="10" height="10"><path d="M1 2h3l1 1h4v6H1z" fill="#f0a81a"/></svg>Public news</span>
      <span><svg width="12" height="10"><ellipse cx="6" cy="5" rx="5" ry="3.5" fill="none" stroke="#f0a81a" stroke-width="1.4"/><circle cx="6" cy="5" r="1.5" fill="#f0a81a"/></svg>24 Views</span>
      <span><svg width="10" height="10"><path d="M5 9 1 5a2 2 0 0 1 4-3 2 2 0 0 1 4 3z" fill="#f0a81a"/></svg>10</span>
    </div>
    <article class="feature">
      <div class="img ph bright" role="img" aria-label="Photo: woman reading on a beach chair"></div>
      <div class="post-title">At vero eos et accusamus et iusto odio dignissimos ducimus quis the lorem</div>
      <div class="meta">Posted by jon · 2 Comments · 9 hours ago</div>
      <p class="excerpt">At vero eos et accusamus et iusto odio dignissimos ducimus qui blanditiis praesentium voluptatum deleniti atque corrupti quos dolores et quas molestias excepturi sint occaecati cupiditate non provident, similique sunt in culpa qui officia deserunt mollitia animi.</p>
      <a class="btn">READ MORE</a>
    </article>
    <div class="meta-row">
      <span><svg width="10" height="10"><rect x="1" y="2" width="8" height="7" fill="none" stroke="#f0a81a" stroke-width="1.4"/></svg>June 5, 2015</span>
      <span><svg width="10" height="10"><path d="M1 1h8v6H4L2 9V7H1z" fill="#f0a81a"/></svg>24 Comments</span>
      <span><svg width="10" height="10"><path d="M1 2h3l1 1h4v6H1z" fill="#f0a81a"/></svg>Public news</span>
      <span><svg width="12" height="10"><ellipse cx="6" cy="5" rx="5" ry="3.5" fill="none" stroke="#f0a81a" stroke-width="1.4"/><circle cx="6" cy="5" r="1.5" fill="#f0a81a"/></svg>24 Views</span>
      <span><svg width="10" height="10"><path d="M5 9 1 5a2 2 0 0 1 4-3 2 2 0 0 1 4 3z" fill="#f0a81a"/></svg>10</span>
    </div>
  </section>

  <div class="pager">Next · 1 · 2</div>
</main>

<div class="abs sidebar">
  <aside class="widget">
    <h3>Recent Post</h3>
    <ul>
      <li>On the other hand we denounce</li>
      <li>At vero eos et accusamus</li>
      <li>Nam libero tempore, cum soluta</li>
      <li>Temporibus autem quibusdam</li>
      <li>Itaque earum rerum hic tenetur</li>
      <li>Lorem ipsum dolor sit amet</li>
      <li>Nemo enim ipsam voluptatem</li>
      <li>Neque porro quisquam est qui</li>
    </ul>
  </aside>
  <aside class="widget">
    <h3>Category</h3>
    <ul>
      <li>Nulla facilisi sed ornare</li>
      <li>Fusce vulputate ante imperdiet</li>
      <li>Morbi finibus diam vitae</li>
      <li class="sub">Mauris vestibulum libero</li>
      <li class="sub">Pellentesque at arcu</li>
      <li class="sub">Praesent pulvinar</li>
      <li class="sub">Vivamus id tortor</li>
      <li>Mauris varius massa</li>
      <li>Morbi vestibulum</li>
      <li>Maecenas consectetur</li>
    </ul>
  </aside>
  <aside class="widget">
    <h3>Most Popular Post</h3>
    <div class="pop"><div class="thumb ph warm" role="img" aria-label="Thumbnail photo"></div><div><div class="t">But I must explain to you how all this mistaken idea</div><div class="meta">Posted on 27th Aug, 2015</div></div></div>
    <div class="pop"><div class="thumb ph" role="img" aria-label="Thumbnail photo"></div><div><div class="t">But I must explain to you how all this mistaken idea</div><div class="meta">Posted on 27th Aug, 2015</div></div></div>
    <div class="pop"><div class="thumb ph cool" role="img" aria-label="Thumbnail photo"></div><div><div class="t">But I must explain to you how all this mistaken idea</div><div class="meta">Posted on 27th Aug, 2015</div></div></div>
    <div class="pop"><div class="thumb ph bright" role="img" aria-label="Thumbnail photo"></div><div><div class="t">But I must explain to you how all this mistaken idea</div><div class="meta">Posted on 27th Aug, 2015</div></div></div>
  </aside>
</div>

<footer class="abs footer">
  <div class="fcol" style="left:120px"><h4>Widget 1</h4><ul><li>Pellentesque at arcu vel nunc</li><li>Nullam quis turpis consectetur</li><li>Mauris fringilla nisl</li><li>Fusce vulputate</li><li>Praesent dapibus augue</li><li>Morbi finibus diam</li></ul></div>
  <div class="fcol" style="left:500px"><h4>Widget 2</h4><ul><li>Pellentesque at arcu vel nunc</li><li>Nullam quis turpis consectetur</li><li>Mauris fringilla nisl</li><li>Fusce vulputate</li><li>Praesent dapibus augue</li><li>Morbi finibus diam</li></ul></div>
  <div class="fcol" style="left:880px"><h4>Widget 3</h4><ul><li>Pellentesque at arcu vel nunc</li><li>Nullam quis turpis consectetur</li><li>Mauris fringilla nisl</li><li>Fusce vulputate</li><li>Praesent dapibus augue</li><li>Morbi finibus diam</li></ul></div>
</footer>
<div class="abs base">
  <div class="copy">Copyright © 2015 Ledger Magazine. All Rights Reserved</div>
  <div class="flinks"><a>Home</a><a>About Us</a><a>Services</a><a>FAQ</a><a>Contact Us</a></div>
</div>

</body>
</html>
```